Fast Growing Personal Injury Law Firm Needs Business Card Design

We need a business card design for a fast growing personal injury law firm in Florida. Our name is Dorian Kalvenfeld, P.A. Our practice is comprised of younger attorneys (in their 30s) that employ more modern techniques/tools than our older competition. We would prefer a look that is a modern play on a classic look. Also, we would like to continue using a color scheme that employs navy blue and kelly green (other shades of green could be fine too) as well as our "E" logo.

Industry/Entity Type

Law Firm

```html
<!DOCTYPE html>
<html lang="en">
<head>
<meta charset="utf-8">
<title>Dorian Kalvenfeld, P.A. — Business Card</title>
<link rel="stylesheet" href="https://fonts.googleapis.com/css2?family=Noto+Serif:ital,wght@0,400;0,700;1,400&display=swap">
<style>
  :root {
    --navy: #1b2f8a;
    --blue: #1f5fb8;
    --blue-light: #3a8fd8;
    --green: #3aa935;
    --green-light: #7cc242;
    --paper: #ffffff;
    --stage: #e9e9ec;
    --ink-soft: #4a4f7a;
  }
  html, body {
    margin: 0;
    width: 1200px;
    height: 768px;
    overflow: hidden;
    background: var(--stage);
    font-family: "Noto Serif", Georgia, serif;
  }
  .stage {
    position: relative;
    width: 1200px;
    height: 768px;
  }
  .card {
    position: absolute;
    top: 230px;
    width: 540px;
    height: 309px;
    background: var(--paper);
    box-shadow: 0 6px 18px rgba(0,0,0,0.18);
    overflow: hidden;
  }
  .card--front { left: 45px; }
  .card--back { left: 615px; }
  .card svg { display: block; }
  .firm-title { font-weight: 700; fill: var(--navy); }
  .firm-practice { font-weight: 700; fill: var(--green); letter-spacing: 0.5px; }
  .attorney-name { font-weight: 700; fill: var(--navy); }
  .attorney-role { font-style: italic; fill: var(--ink-soft); }
  .contact-line { fill: #ffffff; }
  .brand-name { font-weight: 700; fill: var(--navy); }
</style>
</head>
<body>
<main class="stage">

  <section class="card card--front" aria-label="Business card front">
    <svg width="540" height="309" viewBox="0 0 540 309">
      <defs>
        <linearGradient id="frontBlue" x1="0" x2="1">
          <stop offset="0" stop-color="#1b2f8a"/>
          <stop offset="1" stop-color="#3a8fd8"/>
        </linearGradient>
        <linearGradient id="frontGreen" x1="0" x2="1">
          <stop offset="0" stop-color="#3aa935"/>
          <stop offset="1" stop-color="#7cc242"/>
        </linearGradient>
      </defs>
      <g class="front-brand">
        <rect x="170" y="92" width="30" height="30" fill="#1b2f8a"/>
        <text class="brand-name" x="212" y="116" font-size="26">Dorian Kalvenfeld</text>
      </g>
      <path class="front-band-green" d="M0 262 C120 264 230 262 300 272 L300 282 C220 274 110 276 0 276 Z" fill="url(#frontGreen)"/>
      <path class="front-band-blue" d="M250 282 C340 284 440 290 540 290 L540 309 L240 309 Z" fill="url(#frontBlue)"/>
    </svg>
  </section>

  <section class="card card--back" aria-label="Business card back">
    <svg width="540" height="309" viewBox="0 0 540 309">
      <defs>
        <linearGradient id="backBlue" x1="0" x2="1">
          <stop offset="0" stop-color="#1b2f8a"/>
          <stop offset="0.6" stop-color="#1f5fb8"/>
          <stop offset="1" stop-color="#3a8fd8"/>
        </linearGradient>
        <linearGradient id="backGreen" x1="0" x2="1">
          <stop offset="0" stop-color="#3aa935"/>
          <stop offset="1" stop-color="#7cc242"/>
        </linearGradient>
        <linearGradient id="portraitTone" x1="0" y1="0" x2="0" y2="1">
          <stop offset="0" stop-color="#d9c3b0"/>
          <stop offset="0.45" stop-color="#b7a291"/>
          <stop offset="1" stop-color="#2a2d38"/>
        </linearGradient>
      </defs>

      <rect class="brand-square" x="28" y="24" width="56" height="56" fill="#1b2f8a"/>
      <text class="firm-title" x="100" y="56" font-size="24">Dorian Kalvenfeld, P.A.</text>
      <text class="firm-practice" x="100" y="82" font-size="19">Personal Injury Attorneys</text>

      <text class="attorney-name" x="200" y="128" font-size="16">Dorian Kalvenfeld</text>
      <text class="attorney-role" x="200" y="145" font-size="11">Attorney at Law</text>

      <rect class="portrait" x="62" y="92" width="128" height="190" fill="url(#portraitTone)" role="img" aria-label="Portrait photo of the attorney"/>

      <path class="back-blue" d="M0 150 C60 170 110 250 220 262 C300 262 400 182 540 178 L540 309 L0 309 Z" fill="url(#backBlue)"/>
      <path class="back-green" d="M0 138 C60 158 110 238 220 250 C300 250 400 170 540 166" fill="none" stroke="url(#backGreen)" stroke-width="9"/>
      <path class="back-green-thin" d="M0 126 C60 146 110 226 220 238 C300 238 400 158 540 154" fill="none" stroke="#3aa935" stroke-width="3"/>

      <g class="contact" font-size="11.5" text-anchor="end">
        <text class="contact-line" x="502" y="216">941 555 0182</text>
        <text class="contact-line" x="502" y="231">941 555 0147</text>
        <text class="contact-line" x="502" y="246">dorian@kalvenfeldlaw.com</text>
        <text class="contact-line" x="502" y="261">www.kalvenfeldlaw.com</text>
        <text class="contact-line" x="502" y="276">2150 Harbor Crest Way Suite 410</text>
        <text class="contact-line" x="502" y="291">Palmetto Bay, Florida 34299</text>
      </g>

      <g class="contact-icons" fill="#ffffff">
        <path class="icon-phone" d="M512 206 q2 -2 4 0 l2 3 q1 2 -1 3 q1 3 4 4 q1 -2 3 -1 l3 2 q2 2 0 4 q-3 3 -8 -1 q-5 -4 -7 -9 q-1 -3 0 -5 Z"/>
        <rect class="icon-fax" x="512" y="224" width="12" height="8" rx="1"/>
        <rect x="514" y="221" width="8" height="3"/>
        <rect class="icon-mail" x="512" y="238" width="13" height="9" rx="1"/>
        <path d="M512 238 L518.5 244 L525 238" stroke="#1f5fb8" stroke-width="1.2" fill="none"/>
        <circle class="icon-web" cx="518.5" cy="257" r="6"/>
        <path d="M512.5 257 H524.5 M518.5 251 V263" stroke="#1f5fb8" stroke-width="1" fill="none"/>
        <path class="icon-pin" d="M518.5 267 a5 5 0 0 1 5 5 c0 4 -5 9 -5 9 c0 0 -5 -5 -5 -9 a5 5 0 0 1 5 -5 Z"/>
        <circle cx="518.5" cy="272" r="1.8" fill="#1f5fb8"/>
      </g>
    </svg>
  </section>

</main>
</body>
</html>
```